Boutique custom software development company needs new business card

Our nearly 20 year old custom software development company would like to better include the fact that we are now providing Bitcoin services. These new services are B2B include education (how to acquire and securely hold Bitcoin) and integrating Bitcoin payments into existing ecommerce sites or other existing systems. Please keep the card clean and simple. Attached is our current design and some other files. vextorial.com

Target Market(s)

businesses owners interested in long term relationship

Industry/Entity Type

Custom software development and Bitcoin

Contact Information for Business Card

Dale Parker, dale@vextorial.com, vextorial.com, (888) 555-VXTRL

Font styles to use
Other font styles liked:
• monospace

Requirements
Must have
• double-sided
Nice to have
• clean and simple
Should not have
• physical address

```html
<!DOCTYPE html>
<html lang="en">
<head>
<meta charset="utf-8">
<title>Vextorial — Business Card</title>
<link rel="stylesheet" href="https://fonts.googleapis.com/css2?family=Montserrat:wght@400;500;700;800&display=swap">
<style>
  :root {
    --stage: #2b2b2c;
    --card: #1b1c1e;
    --card-back: #141415;
    --pattern: #262628;
    --blue: #3a78c9;
    --orange: #f07c1e;
    --white: #f2f2f2;
    --rule: #5a5a5c;
  }
  * { box-sizing: border-box; margin: 0; padding: 0; }
  html, body { width: 1200px; height: 689px; overflow: hidden; background: var(--stage); }
  body {
    font-family: "Montserrat", sans-serif;
    display: flex; align-items: center; justify-content: center; gap: 60px;
  }
  .card {
    width: 520px; height: 297px; border-radius: 22px;
    position: relative; overflow: hidden;
  }
  .card--back { background: var(--card-back); }
  .card--back .pattern-area {
    position: absolute; inset: 0;
    background: linear-gradient(135deg, var(--pattern), var(--card-back) 70%);
  }
  .card--back .back-mark {
    position: absolute; left: 50%; top: 50%; transform: translate(-50%, -50%);
    color: var(--orange); font-weight: 800; font-size: 30px; letter-spacing: 1px;
  }
  .card--front {
    background: var(--card);
    display: flex; flex-direction: column; align-items: center; justify-content: center;
    color: var(--white);
  }
  .brand-name {
    color: var(--blue); font-weight: 800; font-size: 50px; letter-spacing: 1px; line-height: 1;
  }
  .tagline { color: var(--blue); font-weight: 500; font-size: 15px; margin-top: 2px; }
  .holder-row { display: flex; align-items: center; gap: 14px; margin-top: 18px; }
  .holder-row .rule { width: 34px; height: 1px; background: var(--rule); }
  .holder-name { color: var(--orange); font-weight: 700; font-size: 22px; letter-spacing: 1px; text-transform: uppercase; }
  .icon-row { display: flex; gap: 7px; margin-top: 8px; }
  .icon-row svg { width: 24px; height: 24px; }
  .contact { text-align: center; font-size: 15px; line-height: 1.3; margin-top: 8px; }
  .payment-dot { width: 26px; height: 26px; border-radius: 50%; background: var(--orange); margin-top: 8px; }
</style>
</head>
<body>
  <section class="card card--back" aria-label="Card back">
    <div class="pattern-area" role="img" aria-label="Repeating tone-on-tone brand pattern"></div>
    <span class="back-mark">Vextorial</span>
  </section>

  <section class="card card--front" aria-label="Card front">
    <div class="brand-name">VEXTORIAL</div>
    <div class="tagline">developer of custom applications</div>
    <div class="holder-row">
      <span class="rule"></span>
      <span class="holder-name">Dale Parker</span>
      <span class="rule"></span>
    </div>
    <div class="icon-row">
      <svg viewBox="0 0 24 24" aria-label="Phone"><rect width="24" height="24" rx="5" fill="#3a78c9"/><path d="M8 6l2.5 0 1 3-1.5 1.2a7 7 0 0 0 3.8 3.8L15 12.5l3 1V16a1.5 1.5 0 0 1-1.6 1.5A10.5 10.5 0 0 1 6.5 7.6 1.5 1.5 0 0 1 8 6z" fill="#1b1c1e"/></svg>
      <svg viewBox="0 0 24 24" aria-label="Email"><rect width="24" height="24" rx="5" fill="#3a78c9"/><rect x="5" y="7" width="14" height="10" rx="1" fill="none" stroke="#1b1c1e" stroke-width="1.6"/><path d="M5.5 7.5L12 13l6.5-5.5" fill="none" stroke="#1b1c1e" stroke-width="1.6"/></svg>
      <svg viewBox="0 0 24 24" aria-label="Website"><rect width="24" height="24" rx="5" fill="#3a78c9"/><g fill="none" stroke="#1b1c1e" stroke-width="1.4"><circle cx="12" cy="12" r="6.5"/><ellipse cx="12" cy="12" rx="3" ry="6.5"/><path d="M5.5 12h13M6.5 9h11M6.5 15h11"/></g></svg>
    </div>
    <div class="contact">
      <div>(888) 555-VXTRL</div>
      <div>dale@vextorial.com</div>
      <div>vextorial.com</div>
    </div>
    <div class="payment-dot" aria-hidden="true"></div>
  </section>
</body>
</html>
```